Website for Dental Office - The Bright Arch Clinic

The bright arch clinic is a dental office offering cosmetic dentistry, general dentistry, and multi-specialty dental care all under one roof in our state-of-the-art cosmetic dental center. We are particularly striving to provide services that fit the need of the young generation. Thus, we hope to have a modern, professional concise website that represents our spirit.

*Should be able to switch from English to Chinese

6 sections besides homepage:
Home, Meet us, Services,
Patient Info, Cases&Reviews, Blog, Contact

The Services sections should contain multiple subsections such as cleaning and prevention, cosmetic dentistry, implant dentistry, removable dentures, etc...
The Patient Info section is also intended to contain several subsections such as
New Patient offer, accepted Insurance, patient portal, helpful tips, etc...

Target Market(s)

young generation

Coding

Coded - Design and coding required

Number of Pages Required

5+ page

Font styles to use
Sans Serif

Colors
0592cd
33a6d7
85cae6
00a990
33b8a4
86cfc6
cee9f5
cfeae6
3277b5

Requirements
Must have
• *Should be able to switch from English to Chinese
Nice to have
• http://www.thebrightarchclinic.com/
• As a reference, the above link is the current website, but we would like to change the appearance and the content (our new logo's picture is attached)

```html
<!DOCTYPE html>
<html lang="en">
<head>
<meta charset="utf-8">
<title>The Bright Arch Clinic</title>
<link href="https://fonts.googleapis.com/css2?family=Open+Sans:wght@400;600;700&family=Raleway:wght@600;700&display=swap" rel="stylesheet">
<style>
:root{
  --blue:#0592cd;
  --blue-mid:#33a6d7;
  --blue-light:#85cae6;
  --blue-pale:#cee9f5;
  --green:#00a990;
  --green-mid:#33b8a4;
  --text:#555;
  --heading:#666;
  --dark:#141414;
  --footer-text:#9a9a9a;
}
*{margin:0;padding:0;box-sizing:border-box}
html,body{width:1200px;height:4121px;overflow:hidden}
body{position:relative;font-family:'Open Sans',sans-serif;color:var(--text);background:#fff}
.abs{position:absolute}
a{color:inherit;text-decoration:none}

/* header */
.site-header{position:absolute;left:0;top:0;width:1200px;height:122px;background:#fff}
.brand{left:61px;top:30px;display:flex;align-items:center;gap:14px}
.brand-mark{width:92px;height:50px;background:var(--blue-mid);border-radius:4px}
.brand-name{font-family:'Raleway',sans-serif;font-weight:700;font-size:27px;line-height:28px;color:var(--blue-mid);letter-spacing:.5px}
.phone{left:824px;top:20px;display:flex;align-items:center;gap:12px;font-weight:600;font-size:24px;color:#444}
.phone-icon{width:38px;height:38px;border:2px solid var(--blue);border-radius:50%;display:flex;align-items:center;justify-content:center}
.lang{left:1050px;top:26px;font-size:22px;color:#777;display:flex;align-items:center;gap:8px}
.lang-box{width:26px;height:26px;background:var(--green-mid);border-radius:3px}
.main-nav{left:549px;top:78px;display:flex;gap:22px;font-size:14px;color:#333}
.main-nav .active{color:var(--blue)}

/* hero */
.hero{position:absolute;left:0;top:122px;width:1200px;height:555px;
  background:linear-gradient(100deg,#f3f4f4 0%,#e8eceb 35%,#c9d3d3 55%,#b9c4c8 75%,#8fa2ad 100%)}
.hero-title{left:62px;top:148px;font-family:'Raleway',sans-serif;font-weight:700;font-size:49px;color:var(--blue)}
.hero-quote{left:62px;top:220px;font-weight:600;font-size:34px;color:#333}
.btn{display:inline-flex;align-items:center;justify-content:center;background:var(--blue);color:#fff;font-weight:700;border-radius:40px}
.hero-btn{left:64px;top:291px;width:182px;height:59px;font-size:19px}
.hero-dots{left:572px;top:510px;display:flex;gap:5px}
.hero-dots span{width:10px;height:10px;border-radius:50%;background:#7d8a90}
.hero-dots span.on{background:var(--blue)}

/* section titles */
.section-title{width:1200px;left:0;text-align:center;font-family:'Raleway',sans-serif;font-weight:700;font-size:34px;color:var(--blue)}
.section-intro{width:1200px;left:0;text-align:center;font-size:13px;line-height:27px;color:#555}

/* services */
.service-photo{width:282px;height:282px;border-radius:50%}
.service-arc{width:282px;height:300px}
.service-body{width:526px}
.service-body h3{font-family:'Open Sans',sans-serif;font-weight:600;font-size:22px;letter-spacing:1.5px;color:var(--heading);margin-bottom:14px}
.service-body p{font-size:12.6px;line-height:25px;text-align:justify;margin-bottom:12px}
.service-body .btn{width:113px;height:40px;font-size:12.5px;margin-top:18px}

/* testimonials */
.testimonials{position:absolute;left:0;top:2528px;width:1200px;height:469px;
  background:linear-gradient(180deg,#1b8fd0 0%,#1a9ad8 50%,#178bc6 100%)}
.testi-frame{left:243px;top:186px;width:714px;height:192px;border:2px solid #fff}
.testi-frame::before{content:"";position:absolute;left:300px;top:-4px;width:110px;height:6px;background:#1a96d5}
.testi-avatar{left:558px;top:140px;width:84px;height:84px;border-radius:50%;border:3px solid #fff;background:linear-gradient(160deg,#e8c9a8,#c59a74)}
.testi-name{left:0;top:240px;width:1200px;text-align:center;color:#fff;font-weight:600;font-size:18px}
.testi-text{left:300px;top:274px;width:600px;text-align:center;color:#e9f5fc;font-size:13px;line-height:28px}
.testi-stars{left:0;top:328px;width:1200px;text-align:center}
.testi-more{left:913px;top:248px;display:flex;flex-direction:column;gap:6px}
.testi-more span{width:7px;height:7px;border-radius:50%;background:#fff}

/* patient info */
.info-card{width:242px}
.info-photo{width:242px;height:272px;border:2px solid #dcdcdc}
.info-label{margin-top:16px;text-align:center;font-size:15px;color:#444}

/* footer */
.site-footer{position:absolute;left:0;top:3552px;width:1200px;height:569px;background:var(--dark)}
.news-title{left:0;top:48px;width:1200px;text-align:center;font-family:'Raleway',sans-serif;font-weight:700;font-size:33px;color:#fff}
.news-form{left:368px;top:109px;width:461px;height:43px;border-radius:30px;background:#2a2a2a;display:flex;align-items:center;justify-content:space-between;padding:0 4px 0 32px}
.news-form span{font-size:12px;color:#ccc}
.news-form .btn{width:90px;height:32px;font-size:12.5px}
.footer-rule{left:59px;width:1082px;height:1px;background:#2b2b2b}
.footer-col h4{font-size:13px;font-weight:600;color:#e6e6e6;margin-bottom:14px}
.footer-col li{list-style:none;font-size:11.5px;line-height:24px;color:var(--footer-text)}
.contact-item{display:flex;gap:12px;margin-bottom:14px;font-size:11.5px;line-height:18px;color:var(--footer-text)}
.contact-item b{display:block;color:#e6e6e6;font-weight:600}
.touch-input{width:171px;height:28px;background:#fff;margin-bottom:8px;font-size:8.5px;color:#999;padding:9px 10px}
.touch-btn{width:97px;height:32px;font-size:12px;margin-top:6px}
.social{display:flex;gap:12px;margin-top:18px}
.social span{width:12px;height:12px;border-radius:50%;background:#ddd}
.copyright{left:0;top:534px;width:1200px;text-align:center;font-size:12px;color:#ddd}
</style>
</head>
<body>

<header class="site-header">
  <div class="abs brand">
    <div class="brand-mark"></div>
    <div class="brand-name">THE BRIGHT ARCH<br>CLINIC</div>
  </div>
  <div class="abs phone">
    <span class="phone-icon">
      <svg width="18" height="18" viewBox="0 0 24 24"><path fill="#444" d="M6.6 10.8a15.1 15.1 0 0 0 6.6 6.6l2.2-2.2c.3-.3.7-.4 1-.2 1.1.4 2.3.6 3.6.6.6 0 1 .4 1 1V20c0 .6-.4 1-1 1A17 17 0 0 1 3 4c0-.6.4-1 1-1h3.5c.6 0 1 .4 1 1 0 1.3.2 2.5.6 3.6.1.3 0 .7-.2 1z"/></svg>
    </span>
    555.214.7080
  </div>
  <div class="abs lang">LAN : <span class="lang-box"></span></div>
  <nav class="abs main-nav">
    <a class="active">HOME</a><a>MEET US</a><a>SERVICES</a><a>PATIENT INFO</a><a>CASES &amp; REVIEWS</a><a>BLOG</a><a>CONTACT</a>
  </nav>
</header>

<section class="hero" role="img" aria-label="Smiling senior patient in a dental chair with a dentist holding a dental model">
  <div class="abs hero-title">THE BRIGHT ARCH CLINIC</div>
  <div class="abs hero-quote">“ Your Smile. Our Passion. ”</div>
  <a class="abs btn hero-btn">READ MORE</a>
  <div class="abs hero-dots"><span></span><span class="on"></span><span></span><span></span></div>
</section>

<h2 class="abs section-title" style="top:762px">OUR SERVICES</h2>
<p class="abs section-intro" style="top:820px">Consectetur adipiscing elit, sed do eiusmod tempor incididunt ut labore et dolore magna aliqua. Ut enim ad minim veniam, quis<br>nostrud fugiat nulla pariatur dolore eiusmod tempor incididunt seddao eiusmod incididunt dolore magna aliqua.</p>

<!-- service: cleaning -->
<div class="abs service-photo" style="left:171px;top:947px;background:radial-gradient(circle at 45% 45%,#f4d9c4,#d7a989 70%,#b98a6c)" role="img" aria-label="Smiling woman flossing her teeth"></div>
<svg class="abs service-arc" style="left:171px;top:947px" viewBox="0 0 282 300"><path d="M50 265 A141 141 0 0 0 232 265" fill="none" stroke="var(--green)" stroke-width="4"/></svg>
<div class="abs service-body" style="left:522px;top:955px">
  <h3>CLEANING AND PREVENTION</h3>
  <p>Lorem ipsum dolor sit amet, consectetur adipiscing elit, sed do eiusmod tempor incididunt ut laboret dolore magna eniam, quis nostrud exercitation.</p>
  <p>Consectetur adipiscing elit, sed do eiusmod tempor incididunt ut labore et dolore magna aliqua. Ut enim ad minim veniam, quis nostrud exercitation ul lamco laboris nisi ut aliquip ex ea commodo consequat. Duis aute irure dolor in reprehenderit in voluptate velit esse cillum dolore eu fugiat nulla pariatur dolore.</p>
  <a class="btn">READ MORE</a>
</div>

<!-- service: cosmetic -->
<div class="abs service-body" style="left:170px;top:1355px">
  <h3>COSMETIC DENTISTRY</h3>
  <p>Lorem ipsum dolor sit amet, consectetur adipiscing elit, sed do eiusmod tempor incididunt ut laboret dolore magna eniam, quis nostrud exercitation.</p>
  <p>Consectetur adipiscing elit, sed do eiusmod tempor incididunt ut labore et dolore magna aliqua. Ut enim ad minim veniam, quis nostrud exercitation ul lamco laboris nisi ut aliquip ex ea commodo consequat. Duis aute irure dolor in reprehenderit in voluptate velit esse cillum dolore eu fugiat nulla pariatur dolore.</p>
  <a class="btn">READ MORE</a>
</div>
<div class="abs service-photo" style="left:777px;top:1344px;background:radial-gradient(circle at 50% 40%,#f2e6e0,#d9b9a8 60%,#7fb6dc)" role="img" aria-label="Close-up of a smile with a veneer shade sample held by a gloved hand"></div>
<svg class="abs service-arc" style="left:777px;top:1344px" viewBox="0 0 282 300"><path d="M50 265 A141 141 0 0 0 232 265" fill="none" stroke="var(--green)" stroke-width="4"/></svg>

<!-- service: implant -->
<div class="abs service-photo" style="left:171px;top:1739px;background:radial-gradient(circle at 50% 50%,#e9a49a,#cf6b63 60%,#b44c48)" role="img" aria-label="Close-up of a dental implant in a patient's mouth"></div>
<svg class="abs service-arc" style="left:171px;top:1739px" viewBox="0 0 282 300"><path d="M50 265 A141 141 0 0 0 232 265" fill="none" stroke="var(--green)" stroke-width="4"/></svg>
<div class="abs service-body" style="left:522px;top:1749px">
  <h3>IMPLANT DENTISTRY</h3>
  <p>Lorem ipsum dolor sit amet, consectetur adipiscing elit, sed do eiusmod tempor incididunt ut laboret dolore magna eniam, quis nostrud exercitation.</p>
  <p>Consectetur adipiscing elit, sed do eiusmod tempor incididunt ut labore et dolore magna aliqua. Ut enim ad minim veniam, quis nostrud exercitation ul lamco laboris nisi ut aliquip ex ea commodo consequat. Duis aute irure dolor in reprehenderit in voluptate velit esse cillum dolore eu fugiat nulla pariatur dolore.</p>
  <a class="btn">READ MORE</a>
</div>

<!-- service: dentures -->
<div class="abs service-body" style="left:170px;top:2149px">
  <h3>REMOVABLE DENTURES</h3>
  <p>Lorem ipsum dolor sit amet, consectetur adipiscing elit, sed do eiusmod tempor incididunt ut laboret dolore magna eniam, quis nostrud exercitation.</p>
  <p>Consectetur adipiscing elit, sed do eiusmod tempor incididunt ut labore et dolore magna aliqua. Ut enim ad minim veniam, quis nostrud exercitation ul lamco laboris nisi ut aliquip ex ea commodo consequat. Duis aute irure dolor in reprehenderit in voluptate velit esse cillum dolore eu fugiat nulla pariatur dolore.</p>
  <a class="btn">READ MORE</a>
</div>
<div class="abs service-photo" style="left:777px;top:2138px;background:radial-gradient(circle at 40% 40%,#f3ece6,#d6cfc9 55%,#6fb3d9)" role="img" aria-label="Denture models and a dental mirror on a blue surface"></div>
<svg class="abs service-arc" style="left:777px;top:2138px" viewBox="0 0 282 300"><path d="M50 265 A141 141 0 0 0 232 265" fill="none" stroke="var(--green)" stroke-width="4"/></svg>

<!-- testimonials -->
<section class="testimonials" role="img" aria-label="Faint dental clinic scene in blue tones">
  <h2 class="abs section-title" style="top:80px;color:#fff">TESTIMONIALS</h2>
  <div class="abs testi-frame"></div>
  <div class="abs testi-avatar" role="img" aria-label="Portrait of the reviewing patient"></div>
  <div class="abs testi-name">Mara Ellison</div>
  <p class="abs testi-text">Sed ut perspiciatis unde omnis iste natus sit voluptatem accusantium doloremque laudan, totamem aperiam, eaque ipsa inventore veritatis quasi architecto beatae vitae.</p>
  <div class="abs testi-stars">
    <svg width="96" height="16" viewBox="0 0 96 16">
      <g fill="#fff">
        <path id="star" d="M8 1l2.1 4.6 5 .5-3.8 3.3 1.1 4.9L8 11.8 3.6 14.3l1.1-4.9L.9 6.1l5-.5z"/>
        <use href="#star" x="20"/><use href="#star" x="40"/><use href="#star" x="60"/>
      </g>
      <use href="#star" x="80" fill="none" stroke="#fff" stroke-width="1.2"/>
    </svg>
  </div>
  <div class="abs testi-more"><span></span><span></span><span></span></div>
</section>

<!-- patient info -->
<h2 class="abs section-title" style="top:3079px">PATIENT INFO</h2>
<p class="abs section-intro" style="top:3125px;font-size:12px">Lorem ipsum dolor sit amet consectetur adipisicing elit, sed do aeiusmod tempor incididunt</p>
<div class="abs info-card" style="left:59px;top:3168px">
  <div class="info-photo" style="background:linear-gradient(160deg,#efe4d2,#c9a98a)" role="img" aria-label="Smiling woman holding a dental model"></div>
  <div class="info-label">New Patient offer</div>
</div>
<div class="abs info-card" style="left:338px;top:3168px">
  <div class="info-photo" style="background:linear-gradient(160deg,#eef0ec,#b7c2b8)" role="img" aria-label="Couple reviewing insurance papers with a dental assistant"></div>
  <div class="info-label">Accepted Insurance</div>
</div>
<div class="abs info-card" style="left:618px;top:3168px">
  <div class="info-photo" style="background:linear-gradient(160deg,#e9eef1,#8fb1c9)" role="img" aria-label="Patient seated in a dental chair"></div>
  <div class="info-label">Patient Portal</div>
</div>
<div class="abs info-card" style="left:896px;top:3168px">
  <div class="info-photo" style="background:linear-gradient(160deg,#f1f6f9,#b9d7e8)" role="img" aria-label="Hand holding a denture model"></div>
  <div class="info-label">Helpful Tips</div>
</div>

<!-- footer -->
<footer class="site-footer">
  <div class="abs news-title">Sign up for Newsletter</div>
  <div class="abs news-form"><span>Email</span><a class="btn">SUBMIT</a></div>
  <div class="abs footer-rule" style="top:187px"></div>

  <div class="abs footer-col" style="left:219px;top:245px">
    <h4>Quick Links</h4>
    <ul><li>Home</li><li>Meet us</li><li>Services</li><li>Patient Info</li><li>Cases&amp;Reviews</li><li>Blog</li><li>Contact</li></ul>
  </div>
  <div class="abs footer-col" style="left:405px;top:244px">
    <h4>Support</h4>
    <ul><li>Term of use</li><li>Site Map</li><li>Privacy</li><li>Policy</li></ul>
  </div>
  <div class="abs footer-col" style="left:582px;top:245px">
    <h4>Contact Info</h4>
    <div class="contact-item">
      <svg width="12" height="16" viewBox="0 0 12 16"><path fill="#ddd" d="M6 0a6 6 0 0 0-6 6c0 4.5 6 10 6 10s6-5.5 6-10a6 6 0 0 0-6-6zm0 8.5A2.5 2.5 0 1 1 6 3.5a2.5 2.5 0 0 1 0 5z"/></svg>
      <div><b>Address</b>27 Harbor Lane Suite 12<br>Fairview, MA 01990</div>
    </div>
    <div class="contact-item">
      <svg width="12" height="14" viewBox="0 0 24 24"><path fill="#ddd" d="M6.6 10.8a15.1 15.1 0 0 0 6.6 6.6l2.2-2.2c.3-.3.7-.4 1-.2 1.1.4 2.3.6 3.6.6.6 0 1 .4 1 1V20c0 .6-.4 1-1 1A17 17 0 0 1 3 4c0-.6.4-1 1-1h3.5c.6 0 1 .4 1 1 0 1.3.2 2.5.6 3.6.1.3 0 .7-.2 1z"/></svg>
      <div><b>Phone:</b>555.214.7080</div>
    </div>
    <div class="contact-item">
      <svg width="14" height="12" viewBox="0 0 14 12"><path fill="#ddd" d="M0 0h14v12H0z"/><path d="M0 1l7 5 7-5" fill="none" stroke="#141414" stroke-width="1.5"/></svg>
      <div><b>Email:</b>info@thebrightarchclinic.com</div>
    </div>
  </div>
  <div class="abs footer-col" style="left:832px;top:245px">
    <h4>Get In Touch</h4>
    <div class="touch-input">Full Name</div>
    <div class="touch-input">Email Address</div>
    <a class="btn touch-btn">SEND NOW</a>
    <div class="social"><span></span><span></span><span></span><span></span><span></span></div>
  </div>

  <div class="abs footer-rule" style="top:491px"></div>
  <div class="abs copyright">Copyright 2019 | All Rights Reserved | Privacy Policy | Term &amp; Conditions</div>
</footer>

</body>
</html>
```